New Business Card for our Indoor Golf Training Facility

We are looking for designs for a new business card for our indoor golf training facility. Attached is our logo, our logo with our slogan, and here is our elevator pitch (What makes us different from the others) not sure if all the info will fit on one card, maybe you can condense the elevator pitch? here is the info

Elevator Pitch
We work with serious golfers and those that want to be serious golfers…
to make you better, faster, at all phases of the game…
We use the same state-of-the-art technology as professional golfers…
which produces data sets that shows your improvement in real time.
Our facility is available 24/7 to our members, which allows you to improve on your time.

our website: www.birchpinlinks.com

Target Market(s)

Golfers

Font styles to use
Serif
Sans Serif

Colors
ec1f27
f59195
fbd4d5
919191
d3d3d3
1b1b1b

Requirements
Must have
• our logo or our logo with the slogan, elevator pitch (can be condensed or shortened)

```html
<!DOCTYPE html>
<html lang="en">
<head>
<meta charset="utf-8">
<title>Birch Pin Links – Business Card</title>
<link rel="stylesheet" href="https://fonts.googleapis.com/css2?family=Roboto:wght@400;700;900&family=Roboto+Condensed:wght@400;700&display=swap">
<style>
  :root {
    --brand-red: #ec1f27;
    --card-red: #e9403a;
    --pink: #f59195;
    --grey: #919191;
    --light-grey: #d3d3d3;
    --ink: #1b1b1b;
    --body-ink: #3a3a3a;
    --paper: #f4f4f4;
    --backdrop: #e6e2dc;
    --white: #ffffff;
  }
  * { box-sizing: border-box; margin: 0; padding: 0; }
  html, body { width: 1200px; height: 950px; overflow: hidden; }
  body {
    background: var(--backdrop);
    display: flex;
    flex-direction: column;
    align-items: center;
    justify-content: center;
    gap: 50px;
    font-family: "Roboto", Arial, sans-serif;
  }
  .card {
    width: 700px;
    height: 400px;
    border-radius: 26px;
    position: relative;
    box-shadow: 0 6px 18px rgba(0,0,0,0.18);
    overflow: hidden;
  }

  /* Front */
  .card-front { background: var(--paper); color: var(--ink); }
  .brand {
    position: absolute;
    right: 48px;
    top: 42px;
    display: flex;
    align-items: center;
    gap: 14px;
  }
  .brand-ring {
    width: 58px; height: 58px;
    border: 5px solid var(--brand-red);
    border-radius: 50%;
    flex: none;
  }
  .brand-name {
    font-weight: 900;
    font-size: 40px;
    line-height: 1;
    color: var(--brand-red);
    letter-spacing: -0.5px;
  }
  .brand-slogan {
    font-size: 14px;
    color: var(--brand-red);
    margin-top: 4px;
  }
  .top-rule {
    position: absolute;
    left: 48px; right: 48px; top: 140px;
    border-top: 1.5px solid var(--grey);
  }
  .person { position: absolute; left: 48px; bottom: 40px; }
  .person-name {
    font-weight: 700;
    font-size: 24px;
    color: var(--brand-red);
  }
  .person-title {
    font-size: 16px;
    color: var(--grey);
    margin-top: 2px;
  }
  .person-rule {
    width: 250px;
    border-top: 1.5px solid var(--grey);
    margin: 12px 0;
  }
  .contact-line {
    font-size: 15px;
    color: var(--body-ink);
    line-height: 1.7;
  }

  /* Back */
  .card-back { background: var(--card-red); color: var(--white); }
  .back-ring {
    position: absolute;
    left: 50%; top: 34px;
    width: 112px; height: 112px;
    margin-left: -56px;
    border: 9px solid var(--white);
    border-radius: 50%;
  }
  .pitch {
    position: absolute;
    left: 40px; right: 40px; top: 168px;
    text-align: center;
    font-family: "Roboto Condensed", "Arial Narrow", sans-serif;
  }
  .pitch-title {
    font-weight: 700;
    font-size: 26px;
    letter-spacing: 0.5px;
    margin-bottom: 12px;
  }
  .pitch-text {
    font-size: 16px;
    line-height: 1.5;
  }
  .social {
    position: absolute;
    left: 40px; bottom: 30px;
    display: flex; gap: 6px;
  }
  .social-dot {
    width: 16px; height: 16px;
    border: 2px solid var(--white);
    border-radius: 50%;
  }
</style>
</head>
<body>

  <section class="card card-front" aria-label="Business card front">
    <div class="brand">
      <div class="brand-ring"></div>
      <div>
        <div class="brand-name">Birch Pin Links</div>
        <div class="brand-slogan">Play Smarter. Train Harder. Go Lower.</div>
      </div>
    </div>
    <div class="top-rule"></div>
    <div class="person">
      <div class="person-name">Dana Whitfield</div>
      <div class="person-title">CEO/Founder</div>
      <div class="person-rule"></div>
      <p class="contact-line">1480 W. Alder Rd. Unit B4, Fairmont, OH 45018</p>
      <p class="contact-line">P. 513-555-0172 E. info@birchpinlinks.com W. www.birchpinlinks.com</p>
    </div>
  </section>

  <section class="card card-back" aria-label="Business card back">
    <div class="back-ring"></div>
    <div class="pitch">
      <h2 class="pitch-title">ELEVATOR PITCH :</h2>
      <p class="pitch-text">
        We work with serious golfers and those that want to be serious golfers…<br>
        to make you better, faster, at all phases of the game…<br>
        We use the same state-of-the-art technology as professional golfers…<br>
        which produces data sets that shows your improvement in real time.<br>
        Available 24/7 to our members, which allows you to improve on your time.
      </p>
    </div>
    <div class="social">
      <span class="social-dot"></span>
      <span class="social-dot"></span>
    </div>
  </section>

</body>
</html>
```